Business Card for a Dental Office

The design should communicate integrity, quality and reliability. We also want the card look elegant, simple, but still stand out, different from the traditional-dental-office business card.

Industry/Entity Type

Business

```html
<!DOCTYPE html>
<html lang="en">
<head>
<meta charset="utf-8">
<title>Harlow Dental Studio – Business Card</title>
<link rel="stylesheet" href="https://fonts.googleapis.com/css2?family=Arimo:wght@400;700&display=swap">
<style>
  :root {
    --backdrop: #3a3a3c;
    --card-black: #0b0b0b;
    --card-white: #ffffff;
    --gold: #c9a227;
    --gold-soft: #b8963a;
    --ink: #1c1c1c;
    --ink-soft: #5d5d5d;
    --front-text: #d8d8d8;
    --divider: #e6e6e6;
  }
  * { box-sizing: border-box; margin: 0; padding: 0; }
  html, body { width: 1200px; height: 950px; overflow: hidden; }
  body {
    background: var(--backdrop);
    display: flex;
    flex-direction: column;
    align-items: center;
    justify-content: center;
    gap: 50px;
    font-family: "Arimo", Arial, sans-serif;
  }
  .card {
    position: relative;
    width: 700px;
    height: 400px;
    overflow: hidden;
    box-shadow: 0 10px 30px rgba(0,0,0,.35);
  }

  /* Brand block (shared) */
  .brand { display: flex; align-items: center; gap: 14px; }
  .brand-square { background: var(--gold); flex: none; }
  .brand-text { display: flex; flex-direction: column; }
  .brand-name {
    font-family: "Arimo", Arial, sans-serif;
    font-weight: 700;
    line-height: 1.1;
  }
  .brand-tagline {
    font-family: "Arimo", Arial, sans-serif;
    font-weight: 400;
    color: var(--gold-soft);
    line-height: 1.3;
    margin-top: 4px;
  }

  /* Front */
  .card-front { background: var(--card-black); }
  .card-front .brand { position: absolute; left: 150px; top: 140px; }
  .card-front .brand-square { width: 56px; height: 56px; }
  .card-front .brand-name { font-size: 34px; color: #ffffff; }
  .card-front .brand-tagline { font-size: 14px; }
  .front-website {
    position: absolute;
    left: 0; right: 0; bottom: 80px;
    text-align: center;
    color: var(--front-text);
    font-size: 15px;
    letter-spacing: 3px;
  }

  /* Back */
  .card-back { background: var(--card-white); }
  .card-back .divider { position: absolute; inset: 0; }
  .card-back .brand { position: absolute; left: 40px; top: 250px; }
  .card-back .brand-square { width: 38px; height: 38px; }
  .card-back .brand-name { font-size: 21px; color: var(--ink); }
  .card-back .brand-tagline { font-size: 10px; }

  .contact { position: absolute; left: 385px; top: 48px; color: var(--ink-soft); }
  .person-name { font-size: 22px; font-weight: 700; color: var(--ink); }
  .person-role { font-size: 16px; color: var(--gold-soft); margin-top: 4px; }
  .address { font-size: 15px; line-height: 1.45; margin-top: 14px; }
  .contact-list { list-style: none; margin-top: 6px; }
  .contact-list li { display: flex; align-items: center; gap: 10px; font-size: 15px; line-height: 1.55; }
  .contact-list svg { width: 15px; height: 15px; flex: none; fill: var(--ink); }
</style>
</head>
<body>

  <section class="card card-front" aria-label="Business card front">
    <div class="brand">
      <span class="brand-square"></span>
      <div class="brand-text">
        <span class="brand-name">Harlow Dental Studio</span>
        <span class="brand-tagline">Gentle care for every family</span>
      </div>
    </div>
    <p class="front-website">www.harlowdental.com</p>
  </section>

  <section class="card card-back" aria-label="Business card back">
    <svg class="divider" viewBox="0 0 700 400" aria-hidden="true">
      <path d="M330 0 L360 170 L470 400" fill="none" stroke="var(--divider)" stroke-width="2"/>
    </svg>

    <div class="brand">
      <span class="brand-square"></span>
      <div class="brand-text">
        <span class="brand-name">Harlow Dental Studio</span>
        <span class="brand-tagline">Gentle care for every family</span>
      </div>
    </div>

    <div class="contact">
      <p class="person-name">Elena Marsh</p>
      <p class="person-role">President</p>
      <p class="address">4127 Larkfield Avenue<br>Maple Grove, NY 11990</p>
      <ul class="contact-list">
        <li>
          <svg viewBox="0 0 16 16" aria-label="Phone"><path d="M2 5c0-2 2-3 6-3s6 1 6 3v1h-3V5H5v1H2zM4 7h8l2 7H2z"/></svg>
          555 0142 7781
        </li>
        <li>
          <svg viewBox="0 0 16 16" aria-label="Mobile"><path d="M4 1h8v14H4zM5.5 2.5v9h5v-9zM7 12.5h2v1.5H7z" fill-rule="evenodd"/></svg>
          555 0198 3340
        </li>
        <li>
          <svg viewBox="0 0 16 16" aria-label="Fax"><path d="M4 1h6v4H4zM1 6h14v8H1zM3 8v1h3V8z" fill-rule="evenodd"/></svg>
          555 0163 9027
        </li>
        <li>
          <svg viewBox="0 0 16 16" aria-label="Email"><path d="M1 3h14v10H1zM2.5 4.5 8 9l5.5-4.5z" fill-rule="evenodd"/></svg>
          elena@harlowdental.com
        </li>
        <li>
          <svg viewBox="0 0 16 16" aria-label="Website"><circle cx="8" cy="8" r="7"/><path d="M1 8h14M8 1c-3 4-3 10 0 14M8 1c3 4 3 10 0 14" stroke="#fff" stroke-width="1" fill="none"/></svg>
          www.harlowdental.com
        </li>
      </ul>
    </div>
  </section>

</body>
</html>
```